Create the design of Sitelaunch (in photoshop or similar)

*edit* What we wanna see is a sketch of a first page, and then in the end 5 page designs, but the main page will be the big tasks other pages are just basically pop-ups or form. *edit*

We need a web design for our new startup Sitelaunch in turn will be providing web pages to smaller business. So the purpose of the page is to clearly showcase the message in a web 3.0 fashion, good design looks but function should always be the main focus.Further more we are looking for a long term relationship with a good designer / design company that can help us design the future web sites for our customers as well.

We need you to understand web, not just design. You need to be up to date with how web looks and works, and how to make it as simple and easy to use as possible for the customer and at the same time good looking.

Colors and layout are free to choose, but we really like the kind of layout that forkcomet.com has so feel free to be inspired by them.

We want all of the pages design, but the main/landing page will be the big part, the rest are small pages that will use the same design frame as the main page.

PS. We just want the design in photoshop or illustrator format, the website will then be built in word press by word press experts (let us know if you/company also possess this knowledge)

Target Market(s)

Small to medium sized business, mostly owner/entrepreneur driven companies.

Industry/Entity Type

Business

Font styles to use
Other font styles liked:
• Helvetica for the win

Requirements
Must have
• Great and simple design, a child should be able to understand the message and also enjoy reading it. Should be a funny website while still being professional, i.e. see postbadger.com for example.

```html
<!DOCTYPE html>
<html lang="en">
<head>
<meta charset="utf-8">
<title>Sitelaunch – most convenient web ever</title>
<link rel="stylesheet" href="https://fonts.googleapis.com/css2?family=Roboto+Condensed:wght@400;700&family=Arimo:wght@400;700&family=Open+Sans:wght@400;600&display=swap">
<style>
:root{
  --blue:#1f6fa8;
  --blue-light:#2a9ad8;
  --hero-top:#2b93d3;
  --hero-bottom:#3a98e0;
  --ink:#333;
  --muted:#666;
  --panel:#f3f3f3;
  --footer:#4a4748;
  --btn-dark:#4a4a4a;
}
*{box-sizing:border-box;margin:0;padding:0}
html,body{width:1018px;height:1200px;overflow:hidden;background:#fff}
body{position:relative;font-family:"Arimo",Helvetica,sans-serif;color:var(--ink)}
.abs{position:absolute}

.header{left:0;top:0;width:1018px;height:132px;background:linear-gradient(#fff,#f2f2f2)}
.brand{left:120px;top:28px;font-family:"Roboto Condensed",sans-serif;font-size:36px;color:var(--blue);letter-spacing:-.5px}
.tagline{left:120px;top:74px;font-family:"Roboto Condensed",sans-serif;font-size:12px;color:#333}
.call{right:120px;top:24px;font-family:"Roboto Condensed",sans-serif;font-weight:700;font-size:15px;color:var(--blue-light)}
.chat{right:120px;top:57px;width:80px;height:31px;border-radius:4px;background:linear-gradient(#e2e2e2,#b9b9b9);font-family:"Roboto Condensed",sans-serif;font-weight:700;font-size:11px;color:#444;display:flex;align-items:center;justify-content:center;box-shadow:0 1px 2px rgba(0,0,0,.25)}

.hero{left:0;top:132px;width:1018px;height:303px;background:linear-gradient(var(--hero-top),var(--hero-bottom))}
.nav{left:120px;top:116px;width:779px;height:34px;border-radius:17px;background:linear-gradient(#fff,#e6e6e6);box-shadow:0 2px 3px rgba(0,0,0,.2);display:flex;font-family:"Arimo",sans-serif;font-weight:700;font-size:10px;color:#444;z-index:2}
.nav span{display:flex;align-items:center;justify-content:center;border-right:1px solid #d4d4d4}
.nav span:last-child{border-right:0}
.hero-title{left:121px;top:190px;width:350px;font-family:"Roboto Condensed",sans-serif;font-weight:700;font-size:26px;line-height:36px;color:#fff;word-spacing:4px;text-shadow:0 1px 2px rgba(0,0,0,.25)}
.hero-text{left:121px;top:290px;width:290px;font-family:"Roboto Condensed",sans-serif;font-size:11px;line-height:19px;color:#fff;text-shadow:0 1px 1px rgba(0,0,0,.3)}
.learn{left:120px;top:370px;width:114px;height:30px;border-radius:15px;background:linear-gradient(#fff,#dcdcdc);font-family:"Open Sans",sans-serif;font-size:13px;color:var(--blue);display:flex;align-items:center;justify-content:center}
.hero-art{left:424px;top:188px;width:476px;height:247px;border-radius:200px 200px 0 0;background:radial-gradient(ellipse at 50% 70%,#b9dcf4,#7fbfe9 60%,rgba(90,170,230,.4))}
.dots{left:478px;top:446px;display:flex;gap:6px}
.dots i{width:11px;height:11px;border-radius:50%;background:var(--blue-light)}
.dots i:first-child{background:#ddd}

.divider{left:0;top:472px;width:1018px;height:1px;background:#e4e4e4}
.col{top:498px;width:238px}
.col h2{font-family:"Roboto Condensed",sans-serif;font-weight:700;font-size:14px;color:var(--blue);margin-bottom:14px}
.col .photo{width:238px;height:98px;border:1px solid #ccc}
.col p{margin-top:13px;font-family:"Open Sans",sans-serif;font-size:8.5px;line-height:11.5px;color:#555;text-align:justify}
.btn-dark{margin-top:13px;display:inline-flex;align-items:center;gap:6px;height:22px;padding:0 8px;background:var(--btn-dark);border-bottom:2px solid #222;font-family:"Open Sans",sans-serif;font-size:10px;color:#fff}
.btn-dark .disc{width:13px;height:13px;border-radius:50%;background:#7ac143}

.test{left:0;top:742px;width:1018px;height:351px;background:var(--panel)}
.test h3{position:absolute;left:0;top:20px;width:100%;text-align:center;font-family:"Roboto Condensed",sans-serif;font-weight:700;font-size:21px;color:#333}
.test h3 em{font-style:normal;color:var(--blue)}
.test .sub{position:absolute;left:0;top:53px;width:100%;text-align:center;font-family:"Open Sans",sans-serif;font-size:11px;color:#777}
.row{position:absolute;left:122px;width:780px;height:40px}
.row label{position:absolute;left:0;top:10px;font-family:"Roboto Condensed",sans-serif;font-weight:700;font-size:13px;color:#333}
.field{position:absolute;left:188px;top:2px;width:174px;height:27px;background:#fff;border:1px solid #e2e2e2;border-radius:3px;font-family:"Open Sans",sans-serif;font-size:10px;color:#777;padding:7px 13px}
.field.short{width:81px}
.select{position:absolute;left:276px;top:2px;width:86px;height:27px;background:#fff;border:1px solid #e2e2e2;font-family:"Open Sans",sans-serif;font-size:10px;color:#777;padding:6px 12px}
.select b{position:absolute;right:0;top:0;width:24px;height:25px;background:#d6d6d6}
.select b::after{content:"";position:absolute;left:8px;top:11px;border:4px solid transparent;border-top-color:#fff}
.note{position:absolute;left:383px;top:0;width:385px;font-family:"Roboto Condensed",sans-serif;font-size:9.5px;line-height:14px;color:#555}
.calc{left:310px;top:1030px;width:113px;height:30px;border-radius:2px;background:linear-gradient(#2a86c4,#1b5f95);color:#fff;font-family:"Open Sans",sans-serif;font-size:12px;display:flex;align-items:center;justify-content:center}
.prices{left:505px;top:1031px;width:368px;height:40px;border-radius:2px;background:linear-gradient(#5c5c5c,#3e3e3e);color:#fff;font-family:"Roboto Condensed",sans-serif;font-weight:700;font-size:14px;display:flex;align-items:center;justify-content:center}

.footer{left:0;top:1122px;width:1018px;height:78px;background:var(--footer)}
.copy{left:120px;top:1152px;font-family:"Arimo",sans-serif;font-size:10px;color:#fff}
.social{left:746px;top:1149px;display:flex;gap:8px}
.social i{width:24px;height:24px;border-radius:50%}
</style>
</head>
<body>
<header class="abs header"></header>
<div class="abs brand">Sitelaunch</div>
<div class="abs tagline">most convenient web ever</div>
<div class="abs call">CALL US: +555 0100 2020</div>
<div class="abs chat">Chat with us</div>

<section class="abs hero"></section>
<nav class="abs nav">
  <span style="width:75px">HOME</span><span style="width:107px">SOLUTION</span><span style="width:104px">PRODUCT</span><span style="width:85px">NEWS</span><span style="width:124px">TESTIMONIALS</span><span style="width:72px">FAQ</span><span style="width:110px">PARTNERS</span><span style="width:102px">CONTACT US</span>
</nav>
<h1 class="abs hero-title">At vero eos et accusamus et iusto odiodignissimos ducimus</h1>
<p class="abs hero-text">On the other hand, we denounce with righteous indignation and dislike men who are so beguiled and demoralized by the &nbsp;and trouble that are &nbsp;and I blame belongs to those who fail in their</p>
<div class="abs learn">LEARN MORE</div>
<div class="abs hero-art" role="img" aria-label="Illustration of a desktop monitor, a server stack and a laptop in front of soft blue clouds"></div>
<div class="abs dots"><i></i><i></i><i></i></div>
<div class="abs divider"></div>

<article class="abs col" style="left:119px">
  <h2>WHAT IS SITELAUNCH?</h2>
  <div class="photo" role="img" aria-label="Photo of a businessman in a suit holding a sign, with a red question mark behind him" style="background:linear-gradient(90deg,#4a4f52,#2f3336 60%,#3a2a2a)"></div>
  <p>Sed ut perspiciatis unde omnis iste natus error sit volupta-tem accusantium doloremque laudantium, totam rem aperiam,</p>
  <span class="btn-dark">READ MORE</span>
</article>
<article class="abs col" style="left:389px">
  <h2>WHAT DOES IT COST?</h2>
  <div class="photo" role="img" aria-label="Photo of a pile of banknote bundles" style="background:linear-gradient(#e8e8e0,#b9bda8 50%,#d8d6c4)"></div>
  <p>Sed ut perspiciatis unde omnis iste natus error sit volupta-tem accusantium doloremque laudantium, totam rem aperiam,</p>
  <span class="btn-dark">ORDER NOW</span>
</article>
<article class="abs col" style="left:659px">
  <h2>IF YOU ARE UNHAPPY?</h2>
  <div class="photo" role="img" aria-label="Photo of a stressed office worker sitting at a laptop" style="background:linear-gradient(90deg,#8fa3a8,#c9d3d6 55%,#efefef)"></div>
  <p>Sed ut perspiciatis unde omnis iste natus error sit volupta-tem accusantium doloremque laudantium, totam rem aperiam,</p>
  <span class="btn-dark"><span class="disc"></span>TUNEWAVE</span>
</article>

<section class="abs test">
  <h3>Test your <em>website now!</em></h3>
  <p class="sub">How many more customers could you get every month?</p>
  <div class="row" style="top:103px"><label>Visitors per month</label><div class="field">100000</div><p class="note">(If you can't remember, put in 10 000. Number of visitors to yourwebsite monthly.)</p></div>
  <div class="row" style="top:148px"><label>Current conversion rate in %</label><div class="field">15%</div><p class="note">(If you can't remember put in a 1. The percentage of the visitors to your web that ends up doing something interesting, for example buying your product or service.)</p></div>
  <div class="row" style="top:193px"><label>Improve conversion rate, 13%</label><div class="field">13%</div><p class="note">(let's aim for 13%, a typical increase is around 2%. Better web has a clear purpose, is up to date and easy to understand, that means better conversion.)</p></div>
  <div class="row" style="top:237px"><label style="top:12px">Average purchase in SEK</label><div class="field short" style="top:4px">100</div><div class="select" style="top:3px">SEK<b></b></div><p class="note">(what is the average amount a customer spends with your company within the first year, it can range from 100 100 000+, if you can't remember then guestimate)</p></div>
</section>
<div class="abs calc">Calculate</div>
<div class="abs prices">See prices and details for “MOST CONVENIENT WEB EVER”</div>

<footer class="abs footer"></footer>
<div class="abs copy">© 2014 Sitelaunch. All rights reserved.</div>
<div class="abs social">
  <i style="background:#3b5998"></i><i style="background:#2aa9e0"></i><i style="background:#1a7bb9"></i><i style="background:#e43b2c"></i><i style="background:#f28b1e"></i>
</div>
</body>
</html>
```